At Home Pet Euthanasia - business cards & brand stationary

We already have a logo and the colors and a website. Need a business card designed that will be able to customized to multiple veterinarians who will be partnering with us. The feel needs to be compassionate, comforting with our tagline 'A Gift of Love at Home'. It will be 2 sides.
On the back our platform/partner vets will be customizing each business card with their own service areas, phone numbers, name and title. On the front, i would like to see experimentation with use of our photos, the logo, tagline and a description 'Peaceful and Compassionate At-Home Pet Euthanasia'

```html
<!DOCTYPE html>
<html lang="en">
<head>
<meta charset="utf-8">
<title>RestfulPaw Business Card</title>
<link href="https://fonts.googleapis.com/css2?family=Poppins:wght@400;500;600&display=swap" rel="stylesheet">
<style>
  :root {
    --stage: #202020;
    --brand-blue: #7294bf;
    --band-blue: #7899c2;
    --front-paper: #eef3fa;
    --paper: #ffffff;
    --white: #ffffff;
    --photo-light: #dde5f0;
    --photo-mid: #8f9cb4;
    --photo-dark: #2b3246;
  }
  * { margin: 0; padding: 0; box-sizing: border-box; }
  html, body { width: 1200px; height: 1015px; overflow: hidden; }
  body {
    background: var(--stage);
    font-family: "Poppins", sans-serif;
    display: flex;
    flex-direction: column;
    align-items: center;
    justify-content: center;
    gap: 60px;
  }
  .card {
    width: 680px;
    height: 389px;
    position: relative;
    overflow: hidden;
    box-shadow: 0 10px 30px rgba(0,0,0,0.5);
  }

  /* Front */
  .card-front { background: var(--front-paper); }
  .front-photo {
    position: absolute;
    right: 0; top: 0;
    width: 44%; height: 100%;
    background: linear-gradient(100deg, var(--front-paper) 0%, var(--photo-light) 22%, var(--photo-mid) 55%, var(--photo-dark) 100%);
  }
  .front-brand {
    position: absolute;
    left: 44px; top: 206px;
    display: flex; align-items: center; gap: 12px;
  }
  .brand-dot {
    width: 40px; height: 40px;
    background: var(--brand-blue);
    border-radius: 50%;
    flex: none;
  }
  .brand-name {
    font-weight: 600;
    color: var(--brand-blue);
    letter-spacing: 0.3px;
    line-height: 1;
  }
  .front-brand .brand-name { font-size: 42px; }
  .front-description {
    position: absolute;
    left: 60px; top: 276px;
    color: var(--brand-blue);
    font-size: 17px;
    font-weight: 500;
    line-height: 1.3;
    text-align: center;
    letter-spacing: 0.4px;
  }

  /* Back */
  .card-back { background: var(--paper); display: flex; }
  .back-identity {
    width: 46%;
    display: flex; flex-direction: column;
    align-items: center; justify-content: center;
    gap: 14px;
    padding: 0 24px;
  }
  .back-identity .brand-dot { width: 84px; height: 84px; }
  .back-identity .brand-name { font-size: 40px; }
  .tagline {
    color: var(--brand-blue);
    font-size: 16px;
    font-weight: 400;
    margin-top: -4px;
  }
  .back-contact {
    width: 54%;
    background: var(--band-blue);
    color: var(--white);
    padding: 70px 0 0 44px;
  }
  .person-name { font-size: 25px; font-weight: 600; line-height: 1.1; }
  .person-title { font-size: 17px; font-weight: 400; margin-bottom: 20px; }
  .contact-list { list-style: none; font-size: 16px; line-height: 1.55; }
  .contact-list li { display: flex; align-items: center; gap: 10px; }
  .contact-list svg { width: 16px; height: 16px; flex: none; }
  .address { font-size: 16px; line-height: 1.35; margin-top: 14px; padding-left: 26px; }
</style>
</head>
<body>

  <section class="card card-front">
    <div class="front-photo" role="img" aria-label="Photograph of a senior black dog in a pale collar, gazing to the left against a soft light background"></div>
    <div class="front-brand">
      <span class="brand-dot"></span>
      <span class="brand-name">RestfulPaw</span>
    </div>
    <p class="front-description">Peaceful and Compassionate<br>At-Home Pet Euthanasia</p>
  </section>

  <section class="card card-back">
    <div class="back-identity">
      <span class="brand-dot"></span>
      <span class="brand-name">RestfulPaw</span>
      <span class="tagline">A gift of love at home.</span>
    </div>
    <div class="back-contact">
      <h2 class="person-name">Daniel Hart</h2>
      <p class="person-title">Managing Director</p>
      <ul class="contact-list">
        <li>
          <svg viewBox="0 0 24 24" fill="none" stroke="currentColor" stroke-width="2" stroke-linecap="round" stroke-linejoin="round"><path d="M22 16.9v3a2 2 0 0 1-2.2 2 19.8 19.8 0 0 1-8.6-3.1 19.5 19.5 0 0 1-6-6A19.8 19.8 0 0 1 2.1 4.2 2 2 0 0 1 4.1 2h3a2 2 0 0 1 2 1.7c.1 1 .4 1.9.7 2.8a2 2 0 0 1-.5 2.1L8 9.9a16 16 0 0 0 6 6l1.3-1.3a2 2 0 0 1 2.1-.4c.9.3 1.8.6 2.8.7a2 2 0 0 1 1.7 2z"/></svg>
          044-555 010 246
        </li>
        <li>
          <svg viewBox="0 0 24 24" fill="none" stroke="currentColor" stroke-width="2" stroke-linejoin="round"><rect x="2" y="5" width="20" height="14" rx="1"/><path d="M2 6l10 7 10-7"/></svg>
          info@restfulpaw.com
        </li>
        <li>
          <svg viewBox="0 0 24 24" fill="none" stroke="currentColor" stroke-width="2"><circle cx="12" cy="12" r="10"/><path d="M2 12h20M12 2a15 15 0 0 1 0 20M12 2a15 15 0 0 0 0 20"/></svg>
          www.restfulpaw.com
        </li>
      </ul>
      <p class="address">421, Address line goes here<br>45452, Country Name</p>
    </div>
  </section>

</body>
</html>
```